Request for Business Card Design

Hi. My name is Marlene, I am looking for a new business card design for my company, Quarrow Signal Instruments, LLC. I really like the design you did for Tarsel Venture and was hoping you could do something similar using our full logo and our mark. I am also open to any raised texture design using our mark. I have attached our full logo, which would need to be somewhere on the card, as well as the mark in both outline and full form, as well as our brand colors / guide. The card does not have to be white, as long as our logo and mark appear. I actually like darker colored business cards more, but am open to all options. If you are interested in working with me, please let me know. We would also take the business card design into letterhead design if you can do that.

```html
<!DOCTYPE html>
<html lang="en">
<head>
<meta charset="utf-8">
<title>Quarrow Signal Instruments — Business Card</title>
<link href="https://fonts.googleapis.com/css2?family=Roboto:wght@400;500&display=swap" rel="stylesheet">
<style>
  :root {
    --backdrop: #b8b8b8;
    --card: #000000;
    --ink-grey: #8a8a8a;
    --logo-grey: #6e6e6e;
    --brand-cyan: #1aa3cc;
    --rule: #555555;
    --deco-top: #1c1c1c;
    --deco-bottom: #0a0a0a;
  }
  * { margin: 0; padding: 0; box-sizing: border-box; }
  html, body { width: 1200px; height: 1200px; overflow: hidden; }
  body {
    background: var(--backdrop);
    font-family: "Roboto", Arial, sans-serif;
    position: relative;
  }
  .card {
    position: absolute;
    top: 303px;
    width: 368px;
    height: 594px;
    background: var(--card);
    box-shadow: 4px 4px 5px rgba(0,0,0,0.35);
    overflow: hidden;
  }
  .card--front { left: 200px; }
  .card--back { left: 599px; }

  /* front */
  .front-decoration {
    position: absolute;
    inset: 0;
    background: radial-gradient(ellipse at 60% 55%, var(--deco-top) 0%, var(--deco-bottom) 65%, #000 100%);
  }
  .wordmark {
    position: absolute;
    display: flex;
    align-items: center;
    gap: 18px;
  }
  .wordmark__dot {
    flex: none;
    border-radius: 50%;
    background: var(--brand-cyan);
  }
  .wordmark__name {
    color: var(--logo-grey);
    font-weight: 500;
    text-transform: uppercase;
    line-height: 1;
  }
  .wordmark__name .line-main { display: block; }
  .wordmark__name .line-sub { display: block; }

  .card--front .wordmark { left: 36px; top: 492px; }
  .card--front .wordmark__dot { width: 58px; height: 58px; }
  .card--front .line-main { font-size: 34px; letter-spacing: 6px; }
  .card--front .line-sub { font-size: 12px; letter-spacing: 2px; margin-top: 8px; }

  /* back */
  .back-logo {
    position: absolute;
    left: 0; right: 0; top: 98px;
    display: flex;
    flex-direction: column;
    align-items: center;
  }
  .back-logo .wordmark__dot { width: 70px; height: 70px; }
  .back-logo .wordmark__name { text-align: center; margin-top: 28px; }
  .back-logo .line-main { font-size: 42px; letter-spacing: 7px; }
  .back-logo .line-sub { font-size: 14px; letter-spacing: 2.4px; margin-top: 10px; }

  .person {
    position: absolute;
    left: 0; right: 0; top: 332px;
    text-align: center;
  }
  .person__name {
    color: var(--brand-cyan);
    font-size: 27px;
    font-weight: 500;
    letter-spacing: 0.3px;
    line-height: 1;
  }
  .person__role {
    color: var(--ink-grey);
    font-size: 16px;
    margin-top: 6px;
  }
  .contact-icons {
    position: absolute;
    left: 0; right: 0; top: 395px;
    display: flex;
    justify-content: center;
    align-items: center;
    gap: 4px;
  }
  .contact-icons .rule-piece { width: 52px; height: 1px; background: var(--rule); margin: 0 3px; }
  .icon-box {
    width: 25px; height: 25px;
    background: var(--brand-cyan);
    border-radius: 3px;
    display: flex; align-items: center; justify-content: center;
  }
  .contact-lines {
    position: absolute;
    left: 0; right: 0; top: 428px;
    text-align: center;
    color: var(--ink-grey);
    font-size: 16px;
    line-height: 21px;
  }
  .divider {
    position: absolute;
    left: 88px; width: 195px; top: 507px;
    height: 1px; background: var(--rule);
  }
  .address {
    position: absolute;
    left: 0; right: 0; top: 521px;
    text-align: center;
    color: var(--ink-grey);
    font-size: 16px;
    line-height: 21px;
  }
</style>
</head>
<body>

<section class="card card--front">
  <div class="front-decoration" role="img" aria-label="Large faint brand mark decoration"></div>
  <div class="wordmark">
    <span class="wordmark__dot"></span>
    <span class="wordmark__name">
      <span class="line-main">Quarrow</span>
      <span class="line-sub">Signal Instruments</span>
    </span>
  </div>
</section>

<section class="card card--back">
  <div class="back-logo">
    <span class="wordmark__dot"></span>
    <span class="wordmark__name">
      <span class="line-main">Quarrow</span>
      <span class="line-sub">Signal Instruments</span>
    </span>
  </div>

  <div class="person">
    <p class="person__name">ELIAS BRANDT</p>
    <p class="person__role">Managing Director</p>
  </div>

  <div class="contact-icons">
    <span class="rule-piece"></span>
    <span class="icon-box">
      <svg width="16" height="14" viewBox="0 0 16 14" aria-label="Phone">
        <path d="M1 5 Q8 0 15 5 L13 7 L11 5 L5 5 L3 7 Z" fill="#000"/>
        <rect x="3" y="7" width="10" height="6" rx="1" fill="#000"/>
      </svg>
    </span>
    <span class="icon-box">
      <svg width="16" height="12" viewBox="0 0 16 12" aria-label="Email">
        <rect x="0.75" y="0.75" width="14.5" height="10.5" fill="none" stroke="#000" stroke-width="1.5"/>
        <path d="M1 1 L8 7 L15 1 M1 11 L6 5.5 M15 11 L10 5.5" fill="none" stroke="#000" stroke-width="1.2"/>
      </svg>
    </span>
    <span class="icon-box">
      <svg width="16" height="16" viewBox="0 0 16 16" aria-label="Website">
        <circle cx="8" cy="8" r="7" fill="#000"/>
        <path d="M5 4 Q8 3 9 6 Q7 8 5 7 Z M10 10 Q12 9 12 12 Q10 13 10 10 Z" fill="var(--brand-cyan)"/>
      </svg>
    </span>
    <span class="rule-piece"></span>
  </div>

  <div class="contact-lines">
    <p>044-555 010 234</p>
    <p>info@quarrowsignal.example</p>
    <p>www.quarrowsignal.example</p>
  </div>

  <div class="divider"></div>

  <div class="address">
    <p>17, Harrowgate Lane, Unit 4</p>
    <p>73160, Northland</p>
  </div>
</section>

</body>
</html>
```